Corvane Lending Partners. Professional and Established Company

A full service finance company specializing in obtaining capital for small business. Business Lending advisor, helping small business owners access the capital they need to launch, grow, or sustain their business. Many of our programs offer flexible guidelines to overcome common obstacles such as credit score, credit history, and time in business, financials, and industry type. Our streamlined funding process makes getting a business loan, business line of credit, stated income commercial real estate loan, a smooth and stress free experience.SOME OF THE MOST COMMON NEEDS FOR BUSINESS CAPITAL:• Working Capital• Debt Consolidations (loans, merchant cash advances, etc.)• Payroll• Operating Expenses• Inventory• Equipment Financing• Commercial Real Estate (Purchase, Fix & Flip, Rehab, Renovations)• Business Acquisitions• Business ExpansionWe like the websites:www.quillmorecf.com they are in the same industry and provide the same servicesWe are wanting to be able to update when we do press releases and such using Word Press. Our look should be very professional and we will be adding Our Team Professional Bios and Headshots.

Industry/Entity Type

Finance

Number of Pages Required

5+ page

Font styles to use
Serif
Sans Serif

Requirements
Must have
• We want to copy quillmorecf.com
• We need:
• Home Page
• About Us
• Loan Programs
• Loan Criteria
• News
• Apply Now
• Contact
Nice to have
• See quillmorecf.com
Should not have
• Need professional design. Nothing bright or abstract

```html
<!DOCTYPE html>
<html lang="en">
<head>
<meta charset="utf-8">
<title>Corvane Lending Partners</title>
<link href="https://fonts.googleapis.com/css2?family=Cinzel:wght@400;600&family=Jost:wght@400;500&family=Libre+Baskerville&display=swap" rel="stylesheet">
<style>
:root{
  --blue:#2a6db3;
  --blue-dark:#1d5a9e;
  --navy:#0d1f44;
  --ink:#222;
  --muted:#555;
  --white:#fff;
  --line:#d6d6d6;
}
*{margin:0;padding:0;box-sizing:border-box}
html,body{width:1200px;height:2913px;overflow:hidden;background:var(--white)}
body{position:relative;font-family:'Jost',sans-serif;color:var(--ink)}
.abs{position:absolute}
.brand{font-family:'Cinzel',serif;font-weight:600;color:var(--blue);line-height:1.05;letter-spacing:1px}
.brand .big{display:block;font-size:32px}
.brand .small{display:block;font-size:14px;letter-spacing:3.5px}
.nav{display:flex;gap:24px;font-family:'Cinzel',serif;font-size:12.5px;color:var(--ink);letter-spacing:.6px;white-space:nowrap}
.contact-bar{display:flex;align-items:center;gap:22px;font-size:12.5px;color:var(--muted);white-space:nowrap}
.contact-bar span{display:flex;align-items:center;gap:7px}
.social{display:flex;gap:5px}
.social i{width:24px;height:24px;border-radius:50%;background:var(--blue)}
.photo{display:block}
.hero{left:0;top:97px;width:1200px;height:501px;
  background:
    radial-gradient(ellipse 260px 170px at 900px 330px,rgba(226,170,70,.55),transparent 70%),
    radial-gradient(ellipse 300px 220px at 250px 230px,rgba(90,150,210,.45),transparent 70%),
    radial-gradient(ellipse 260px 260px at 620px 160px,rgba(120,170,220,.35),transparent 70%),
    linear-gradient(180deg,#0b2150 0%,#1b3f78 35%,#23466f 62%,#1d3a2c 78%,#1a2433 90%,#0e1522 100%)}
.hero-text{left:0;top:265px;width:1200px;text-align:center;color:var(--white);font-family:'Libre Baskerville',serif;font-weight:400;font-size:27px;line-height:40px}
.hero-cta{left:0;top:404px;width:1200px;text-align:center;font-family:'Cinzel',serif;font-size:16px;color:var(--white);text-decoration:underline;text-underline-offset:5px;letter-spacing:1px}
.video-line{left:0;top:635px;width:1200px;text-align:center;font-size:21px;color:#333}
.video-line a{color:var(--blue);text-decoration:none}
.news-panel{color:var(--white);padding-top:57px;
  background:
    linear-gradient(125deg,transparent 30%,rgba(70,130,220,.35) 45%,transparent 60%),
    linear-gradient(100deg,#050d22 0%,#0f2d6a 30%,#2457a6 60%,#0a1c44 85%,#050b1c 100%)}
.news-label{font-size:14px;margin-bottom:4px}
.news-title{font-size:17px;line-height:26px;margin-bottom:10px;font-weight:400}
.news-body{width:460px;font-size:11.6px;line-height:20px;opacity:.92}
.news-more{margin-top:10px;font-family:'Cinzel',serif;font-size:13px;text-decoration:underline;text-underline-offset:4px;letter-spacing:1px}
.section-title{left:0;top:1424px;width:1200px;text-align:center;font-family:'Cinzel',serif;font-weight:600;font-size:23px;color:var(--blue-dark);letter-spacing:1.5px}
.program{width:400px;text-align:center}
.program .photo{width:400px;height:267px}
.program h3{margin-top:15px;font-family:'Cinzel',serif;font-weight:600;font-size:18px;color:var(--blue-dark);letter-spacing:1px}
.program p{margin-top:4px;font-size:12.5px;line-height:19px;color:var(--ink)}
.view-link{left:0;top:2676px;width:1200px;text-align:center;font-family:'Cinzel',serif;font-weight:600;font-size:14px;color:var(--blue);text-decoration:underline;text-underline-offset:4px;letter-spacing:1px}
.footer-rule{left:140px;top:2764px;width:918px;height:1px;background:var(--line)}
.copyright{left:0;top:2872px;width:1200px;height:41px;background:var(--blue);color:var(--white);font-size:11.5px;text-align:center;line-height:41px}
</style>
</head>
<body>

<header>
  <div class="abs brand" style="left:142px;top:20px">
    <span class="big">CORVANE</span>
    <span class="small">LENDING PARTNERS</span>
  </div>
  <div class="abs contact-bar" style="right:142px;top:17px">
    <span>
      <svg width="14" height="14" viewBox="0 0 24 24"><path fill="#2a6db3" d="M6.6 10.8a15.1 15.1 0 0 0 6.6 6.6l2.2-2.2c.3-.3.7-.4 1-.2 1.1.4 2.3.6 3.6.6.6 0 1 .4 1 1V20c0 .6-.4 1-1 1A17 17 0 0 1 3 4c0-.6.4-1 1-1h3.5c.6 0 1 .4 1 1 0 1.3.2 2.5.6 3.6.1.3 0 .7-.2 1z"/></svg>
      123-456-7890
    </span>
    <span>
      <svg width="15" height="12" viewBox="0 0 24 18"><rect x="1" y="1" width="22" height="16" rx="2" fill="#2a6db3"/><path d="M2 2l10 8 10-8" stroke="#fff" stroke-width="2" fill="none"/></svg>
      info@corvanelending.com
    </span>
    <div class="social"><i></i><i></i><i></i></div>
  </div>
  <nav class="abs nav" style="right:142px;top:67px">
    <span>HOME</span><span>ABOUT</span><span>LOAN PROGRAMS</span><span>LOAN CRITERIA</span><span>NEWS</span><span>APPLY NOW</span><span>CONTACT</span>
  </nav>
</header>

<section>
  <div class="abs photo hero" role="img" aria-label="Glass office towers lit at dusk with trees and a plaza in front"></div>
  <h1 class="abs hero-text">We Are Full Service Finance Company<br>Specializing In Obtaining Capital For<br>Small Business.</h1>
  <div class="abs hero-cta">Contact Us Today</div>
</section>

<p class="abs video-line"><a href="#">Click here</a> for a comprehensive video of our services.</p>

<section>
  <article class="abs news-panel" style="left:0;top:703px;width:643px;height:328px;padding-left:141px" role="img" aria-label="Blue skyscrapers seen from below behind the news text">
    <div class="news-label">Recent News</div>
    <div class="news-title">Lorem ipsum dolor sit amet, consectetuer adipiscing elit,<br>sed diam nonummy nibh euismod tincidunt ut.</div>
    <div class="news-body">Lorem ipsum dolor sit amet, consectetuer adipiscing elit, sed diam nonummy nibh euismod tincidunt ut laoreet dolore magna aliquam erat volutpat. Ut wisi enim ad minim veniam, quis nostrud exerci tation ullamcorper suscipit lobortis nisl ut aliquip ex ea commodo consequat. Duis autem vel eum iriure dolor in hendrerit in vulputate velit esse molestie consequat vel illum dolore eu.</div>
    <div class="news-more">READ MORE</div>
  </article>
  <div class="abs photo" style="left:643px;top:703px;width:557px;height:328px;background:
    radial-gradient(ellipse 120px 140px at 80px 230px,rgba(40,80,30,.7),transparent 70%),
    linear-gradient(90deg,#3a2a22 0%,#4d3a30 12%,transparent 22%),
    linear-gradient(180deg,#2f66c2 0%,#4a7fc8 30%,#5f7d9c 55%,#4d5560 75%,#9a968e 88%,#d4d0c8 100%)" role="img" aria-label="Modern glass office building with pedestrians on the street"></div>

  <div class="abs photo" style="left:0;top:1033px;width:557px;height:328px;background:
    radial-gradient(ellipse 220px 90px at 240px 170px,rgba(210,215,220,.8),transparent 70%),
    linear-gradient(180deg,#5d94d6 0%,#9cc0e6 25%,#cfdbe4 42%,#8e9aa3 60%,#6c7378 75%,#b59a7c 90%,#c9b08f 100%)" role="img" aria-label="Curved glass and stone campus building under a blue sky"></div>
  <article class="abs news-panel" style="left:557px;top:1033px;width:643px;height:328px;padding-left:43px" role="img" aria-label="Blue skyscrapers seen from below behind the news text">
    <div class="news-label">Recent News</div>
    <div class="news-title">Lorem ipsum dolor sit amet, consectetuer adipiscing elit,<br>sed diam nonummy nibh euismod tincidunt ut.</div>
    <div class="news-body">Lorem ipsum dolor sit amet, consectetuer adipiscing elit, sed diam nonummy nibh euismod tincidunt ut laoreet dolore magna aliquam erat volutpat. Ut wisi enim ad minim veniam, quis nostrud exerci tation ullamcorper suscipit lobortis nisl ut aliquip ex ea commodo consequat. Duis autem vel eum iriure dolor in hendrerit in vulputate velit esse molestie consequat vel illum dolore eu.</div>
    <div class="news-more">READ MORE</div>
  </article>
</section>

<section>
  <h2 class="abs section-title">LOAN PROGRAMS</h2>

  <div class="abs program" style="left:0;top:1488px">
    <div class="photo" style="background:
      radial-gradient(ellipse 130px 70px at 200px 120px,rgba(150,170,130,.75),transparent 70%),
      radial-gradient(ellipse 110px 160px at 60px 90px,rgba(40,32,30,.7),transparent 70%),
      linear-gradient(135deg,#d7d6d8 0%,#ecebe9 40%,#c8c6c3 70%,#8c8a86 100%)" role="img" aria-label="Hands passing banknotes across a desk"></div>
    <h3>Working Capital</h3>
    <p>Lorem ipsum dolor sit amet, consectetuer adipiscing elit,<br>sed diam nonummy nibh euismod tincidunt ut.</p>
  </div>
  <div class="abs program" style="left:400px;top:1488px">
    <div class="photo" style="background:
      radial-gradient(ellipse 110px 110px at 240px 110px,rgba(120,150,190,.6),transparent 70%),
      radial-gradient(ellipse 120px 90px at 160px 90px,rgba(200,150,120,.6),transparent 70%),
      linear-gradient(180deg,#e6ece0 0%,#d3dccb 35%,#c8b8a4 60%,#9c7c62 80%,#6f5442 100%)" role="img" aria-label="Smiling couple working on a laptop at home"></div>
    <h3>Debt Consolidations</h3>
    <p>Lorem ipsum dolor sit amet, consectetuer adipiscing elit,<br>sed diam nonummy nibh euismod tincidunt ut.</p>
  </div>
  <div class="abs program" style="left:800px;top:1488px">
    <div class="photo" style="background:
      radial-gradient(ellipse 140px 70px at 150px 220px,rgba(40,140,200,.55),transparent 70%),
      radial-gradient(ellipse 80px 80px at 360px 200px,rgba(30,30,30,.5),transparent 70%),
      linear-gradient(160deg,#f4f4f4 0%,#e4eaee 45%,#c3d6e2 75%,#9dbcd0 100%)" role="img" aria-label="Calculator and financial charts on a desk"></div>
    <h3>Payroll</h3>
    <p>Lorem ipsum dolor sit amet, consectetuer adipiscing elit,<br>sed diam nonummy nibh euismod tincidunt ut.</p>
  </div>

  <div class="abs program" style="left:0;top:1890px">
    <div class="photo" style="background:
      radial-gradient(ellipse 120px 130px at 210px 90px,rgba(220,225,230,.7),transparent 70%),
      radial-gradient(ellipse 160px 60px at 200px 230px,rgba(190,160,100,.65),transparent 70%),
      linear-gradient(180deg,#0b2336 0%,#173a52 45%,#2a4c5c 70%,#4a5a50 100%)" role="img" aria-label="Hands around stacks of coins forming a rising chart"></div>
    <h3>Operating Expenses</h3>
    <p>Lorem ipsum dolor sit amet, consectetuer adipiscing elit,<br>sed diam nonummy nibh euismod tincidunt ut.</p>
  </div>
  <div class="abs program" style="left:400px;top:1890px">
    <div class="photo" style="background:
      radial-gradient(ellipse 90px 110px at 260px 120px,rgba(200,200,195,.55),transparent 70%),
      radial-gradient(ellipse 120px 80px at 120px 220px,rgba(210,150,80,.6),transparent 70%),
      linear-gradient(135deg,#5a3a1e 0%,#94683a 35%,#7a5530 60%,#3a2616 100%)" role="img" aria-label="Worker with a laptop in a warehouse full of boxes"></div>
    <h3>Inventory</h3>
    <p>Lorem ipsum dolor sit amet, consectetuer adipiscing elit,<br>sed diam nonummy nibh euismod tincidunt ut.</p>
  </div>
  <div class="abs program" style="left:800px;top:1890px">
    <div class="photo" style="background:
      radial-gradient(ellipse 120px 70px at 100px 140px,rgba(140,70,50,.55),transparent 70%),
      radial-gradient(ellipse 60px 50px at 260px 170px,rgba(220,180,40,.55),transparent 70%),
      linear-gradient(180deg,#dde4ea 0%,#b8c3cc 30%,#7e8a94 55%,#8b8f92 75%,#a9aaa8 100%)" role="img" aria-label="Worker beside a container truck and forklift at a depot"></div>
    <h3>Equipment Financing</h3>
    <p>Lorem ipsum dolor sit amet, consectetuer adipiscing elit,<br>sed diam nonummy nibh euismod tincidunt ut.</p>
  </div>

  <div class="abs program" style="left:0;top:2292px">
    <div class="photo" style="background:
      radial-gradient(ellipse 110px 110px at 220px 60px,rgba(255,255,245,.9),transparent 70%),
      linear-gradient(90deg,#3e5f8e 0%,#6e8fb8 22%,#c5d6e6 45%,#d9e4ee 55%,#7c9bc0 78%,#3d5c86 100%)" role="img" aria-label="Businessman looking up at office towers"></div>
    <h3>Commercial Real Estate</h3>
    <p>Lorem ipsum dolor sit amet, consectetuer adipiscing elit,<br>sed diam nonummy nibh euismod tincidunt ut.</p>
  </div>
  <div class="abs program" style="left:400px;top:2292px">
    <div class="photo" style="background:
      radial-gradient(ellipse 130px 70px at 200px 180px,rgba(170,165,160,.6),transparent 70%),
      linear-gradient(180deg,#3a3a3d 0%,#2a2a2d 40%,#48484c 70%,#6a6866 100%)" role="img" aria-label="Business team standing behind a handshake"></div>
    <h3>Business Acquisitions</h3>
    <p>Lorem ipsum dolor sit amet, consectetuer adipiscing elit,<br>sed diam nonummy nibh euismod tincidunt ut.</p>
  </div>
  <div class="abs program" style="left:800px;top:2292px">
    <div class="photo" style="background:
      radial-gradient(ellipse 120px 90px at 140px 70px,rgba(235,225,230,.6),transparent 70%),
      radial-gradient(ellipse 110px 80px at 320px 180px,rgba(210,150,130,.55),transparent 70%),
      linear-gradient(135deg,#9a8fb6 0%,#6a6a98 40%,#3b3f68 70%,#2a2c48 100%)" role="img" aria-label="Hands using a tablet and keyboard at a desk"></div>
    <h3>Business Expansion</h3>
    <p>Lorem ipsum dolor sit amet, consectetuer adipiscing elit,<br>sed diam nonummy nibh euismod tincidunt ut.</p>
  </div>

  <div class="abs view-link">VIEW LOAN PROGRAMS</div>
</section>

<footer>
  <div class="abs footer-rule"></div>
  <div class="abs brand" style="left:142px;top:2790px">
    <span class="big">CORVANE</span>
    <span class="small">LENDING PARTNERS</span>
  </div>
  <nav class="abs nav" style="right:142px;top:2810px">
    <span>HOME</span><span>ABOUT</span><span>LOAN PROGRAMS</span><span>LOAN CRITERIA</span><span>NEWS</span><span>APPLY NOW</span><span>CONTACT</span>
  </nav>
  <div class="abs copyright">Copyright © 2018 Corvane Lending Partners. All Rights Reserved.</div>
</footer>

</body>
</html>
```